Appraisal and Umpire Services for Property Damage Insurance Claims

I need a banner design that I can post as an advertisement on industry web pages. I would like this to be elegant and reflective of quality, integrity and professionalism.

Target Market(s)

Insurance Companies and Attorneys

Industry/Entity Type

Insurance

Contact Information for Business Card

Gordon T. Ashby
218 Birchwell Lane
PO Box 913
Clifton Park, NY 12348
gashby@meridaleclaims.com
Phone: (800) 519-4867, Ext. 2716
Direct: (315) 648-9052

Logo Text

Line One: Silver Hollow Claim Service, Inc. Line two: Appraisal and Umpire Services

Font styles to use
Serif
Sans Serif

Colors
0255a3
f78f20
faa54b
3176b5

Requirements
Must have
• New Logo and matching banner, business card and stationary.
• The colors must be orange and navy blue in the logo. I have selected them below.

```html
<!DOCTYPE html>
<html lang="en">
<head>
<meta charset="utf-8">
<title>Silver Hollow Claim Service — Banner Set</title>
<link href="https://fonts.googleapis.com/css2?family=Open+Sans:wght@300;400;700&family=PT+Sans+Narrow:wght@700&display=swap" rel="stylesheet">
<style>
  :root {
    --navy: #0255a3;
    --orange: #f78f20;
    --orange-deep: #f26f0c;
    --white: #ffffff;
    --sheet: #000000;
  }
  html, body {
    margin: 0;
    padding: 0;
    width: 1200px;
    height: 1200px;
    overflow: hidden;
    background: var(--sheet);
  }
  .sheet {
    position: relative;
    width: 1200px;
    height: 1200px;
  }
  .banner {
    position: absolute;
    left: 89px;
    width: 1021px;
    height: 214px;
    display: block;
  }
  .banner--one { top: 202px; }
  .banner--two { top: 495px; }
  .banner--three { top: 799px; }

  .panel { fill: var(--navy); }
  .accent { fill: var(--orange-deep); }
  .brand-square { fill: var(--orange); }
  .brand-name {
    font-family: "Open Sans", sans-serif;
    font-weight: 700;
    font-size: 40px;
    fill: var(--white);
  }
  .brand-line {
    font-family: "Open Sans", sans-serif;
    font-weight: 300;
    font-size: 41px;
    fill: var(--white);
  }
  .contact-head {
    font-family: "Open Sans", sans-serif;
    font-weight: 700;
    font-size: 15.5px;
    fill: var(--white);
  }
  .contact-line {
    font-family: "Open Sans", sans-serif;
    font-weight: 400;
    font-size: 15.5px;
    fill: var(--white);
  }
  .tagline {
    font-family: "PT Sans Narrow", sans-serif;
    font-weight: 700;
    fill: var(--white);
    stroke: rgba(40, 20, 10, 0.55);
    stroke-width: 2px;
    paint-order: stroke;
  }
  .tagline--stack { font-size: 36px; }
  .tagline--wide { font-size: 38px; }
  .tagline--large { font-size: 44px; }
</style>
</head>
<body>
<main class="sheet">

  <!-- Banner one -->
  <svg class="banner banner--one" viewBox="0 0 1021 214" xmlns="http://www.w3.org/2000/svg">
    <defs>
      <linearGradient id="fire-one" x1="0" y1="0" x2="1" y2="1">
        <stop offset="0" stop-color="#6b6f80"/>
        <stop offset="0.35" stop-color="#e2561c"/>
        <stop offset="0.6" stop-color="#3d3a48"/>
        <stop offset="1" stop-color="#c8471d"/>
      </linearGradient>
    </defs>
    <rect class="panel" x="0" y="0" width="1021" height="214"/>
    <polygon points="517,0 1021,0 1021,214 363,214" fill="url(#fire-one)" role="img" aria-label="Photo of a two-storey house engulfed in flames behind bare trees"/>
    <polygon class="accent" points="458,0 517,0 363,214 453,214"/>
    <polygon class="panel" points="0,0 458,0 363,214 0,214"/>
    <rect class="brand-square" x="22" y="36" width="14" height="14"/>
    <text class="brand-name" x="46" y="61">Silver Hollow</text>
    <text class="brand-line" x="37" y="102">Claim Service, Inc</text>
    <text class="contact-head" x="42" y="136">Contact</text>
    <text class="contact-line" x="42" y="154">Gordon T. Ashby</text>
    <text class="contact-line" x="42" y="172">Email: gashby@meridaleclaims.com</text>
    <text class="contact-line" x="42" y="190">Phone: (800) 519-4867, Ext. 2716</text>
    <text class="tagline tagline--stack" x="799" y="114">Appraisal</text>
    <text class="tagline tagline--stack" x="799" y="148">and Umpire</text>
    <text class="tagline tagline--stack" x="799" y="182">Services</text>
  </svg>

  <!-- Banner two -->
  <svg class="banner banner--two" viewBox="0 0 1021 214" xmlns="http://www.w3.org/2000/svg">
    <defs>
      <linearGradient id="fire-two" x1="0" y1="0" x2="0" y2="1">
        <stop offset="0" stop-color="#f07a1c"/>
        <stop offset="0.42" stop-color="#e65a14"/>
        <stop offset="0.55" stop-color="#7a7a80"/>
        <stop offset="0.75" stop-color="#5b3a2c"/>
        <stop offset="1" stop-color="#3c4a2c"/>
      </linearGradient>
    </defs>
    <rect class="panel" x="0" y="0" width="1021" height="214"/>
    <polygon points="517,0 1021,0 1021,214 363,214" fill="url(#fire-two)" role="img" aria-label="Photo of a single-storey brick house with its roof on fire"/>
    <polygon class="accent" points="458,0 517,0 363,214 453,214"/>
    <polygon class="panel" points="0,0 458,0 363,214 0,214"/>
    <rect class="brand-square" x="22" y="36" width="14" height="14"/>
    <text class="brand-name" x="46" y="61">Silver Hollow</text>
    <text class="brand-line" x="37" y="102">Claim Service, Inc</text>
    <text class="contact-head" x="42" y="136">Contact</text>
    <text class="contact-line" x="42" y="154">Gordon T. Ashby</text>
    <text class="contact-line" x="42" y="172">Email: gashby@meridaleclaims.com</text>
    <text class="contact-line" x="42" y="190">Phone: (800) 519-4867, Ext. 2716</text>
    <text class="tagline tagline--wide" x="1001" y="51" text-anchor="end">Appraisal and Umpire Services</text>
  </svg>

  <!-- Banner three -->
  <svg class="banner banner--three" viewBox="0 0 1021 214" xmlns="http://www.w3.org/2000/svg">
    <defs>
      <linearGradient id="fire-three" x1="0" y1="0" x2="1" y2="0">
        <stop offset="0" stop-color="#6a4a3a"/>
        <stop offset="0.35" stop-color="#f0a040"/>
        <stop offset="0.6" stop-color="#e0661e"/>
        <stop offset="0.85" stop-color="#8a4a2e"/>
        <stop offset="1" stop-color="#a7a2a6"/>
      </linearGradient>
    </defs>
    <rect class="panel" x="0" y="0" width="1021" height="214"/>
    <polygon points="517,0 1021,0 1021,214 363,214" fill="url(#fire-three)" role="img" aria-label="Photo of a house burning behind a large bare tree, firefighters nearby"/>
    <polygon class="accent" points="458,0 517,0 363,214 453,214"/>
    <polygon class="panel" points="0,0 458,0 363,214 0,214"/>
    <rect class="brand-square" x="22" y="36" width="14" height="14"/>
    <text class="brand-name" x="46" y="61">Silver Hollow</text>
    <text class="brand-line" x="37" y="102">Claim Service, Inc</text>
    <text class="contact-head" x="42" y="136">Contact</text>
    <text class="contact-line" x="42" y="154">Gordon T. Ashby</text>
    <text class="contact-line" x="42" y="172">Email: gashby@meridaleclaims.com</text>
    <text class="contact-line" x="42" y="190">Phone: (800) 519-4867, Ext. 2716</text>
    <text class="tagline tagline--large" x="988" y="185" text-anchor="end">Appraisal and Umpire Services</text>
  </svg>

</main>
</body>
</html>
```